Health Coaching website focused on diabetes management using Vantelo template

I am starting a health coaching business and would like to use Plumestack and an Vantelo template. The coaching will focus on Pre-diabetic and chronic disease patients so it will need to have a personal as well as a slight clinical look to it. The site should have an overall look similar to Meadow Loop theme. I will purchase the Vantelo designer package for use.

Target Market(s)

40-60 year olds with pre-diabetes or concerned about chronic disease, maintaining health, nutrition and weight loss

Industry/Entity Type

Health And Wellness

Number of Pages Required

5+ page

Colors
87cfc6
60b9df
fee18a
00a990
3276b5

Requirements
Must have
• It should contain an ecommerce tab, member's only area, interactive blog, built-in SEO and an opt-in area on every page. It should have several call to actions throughout the site. The site should have an overall look similar to Meadow Loop theme. Hosting on Servunda. Also needed all the essential plumestack plugins:
• Keystep forms & Keystep entry pages
• Pondra Metrics
• Vantelo shield plus
• Postwren
• Valdeno
• Vault Parrot
• Kindle SEO
• Drifting Share Strip
• Q7 Rapid Store
• Tembi
Nice to have
• Ecommerce ready with cartoflex plugin
• Hi-res pictures of people in my demographic enjoying life and/or exercising, cooking, etc.
Should not have
• slider on homepage
• my profile on homepage

```html
<!DOCTYPE html>
<html lang="en">
<head>
<meta charset="utf-8">
<title>VitaPath Wellness – FAQ's</title>
<link rel="stylesheet" href="https://fonts.googleapis.com/css2?family=Jost:wght@400&family=Open+Sans:wght@400;600;700&display=swap">
<style>
:root{
  --blue:#3276b5;
  --teal:#00a990;
  --teal-dark:#008a75;
  --ink:#222;
  --text:#333;
  --rule:#dcdcdc;
  --crumb:#e8e8e8;
  --hero-bg:#eeebe2;
  --footer:#1f2733;
  --footer-text:#c4c8ce;
  --footer-rule:#3a4350;
  --footer-brand:#8b9099;
}
*{box-sizing:border-box;margin:0;padding:0}
html,body{width:882px;height:1200px;overflow:hidden;background:#fff}
body{position:relative;font-family:"Open Sans",Arial,sans-serif;color:var(--text)}
h1,h2,h3,h4{font-weight:400}
a{color:inherit;text-decoration:none}

.site-header{position:absolute;left:0;top:0;width:882px;height:83px}
.brand{position:absolute;left:118px;top:24px;display:flex;align-items:center;gap:10px}
.brand-mark{width:34px;height:34px;border-radius:50%;background:var(--teal)}
.brand-name{font-family:"Open Sans",Arial,sans-serif;font-weight:400;font-size:20px;line-height:26px;color:var(--ink);white-space:nowrap}
.header-phone{position:absolute;left:460px;top:29px;display:flex;align-items:center;gap:10px;font-size:15px;color:#444}
.phone-badge{width:26px;height:26px;border-radius:50%;background:var(--teal);display:flex;align-items:center;justify-content:center}
.cta-button{position:absolute;left:604px;top:29px;width:160px;height:28px;background:var(--teal);color:#fff;font-size:10.5px;letter-spacing:.2px;display:flex;align-items:center;justify-content:center;gap:7px;border-bottom:2px solid var(--teal-dark)}

.main-nav{position:absolute;left:0;top:83px;width:882px;height:27px;background:var(--blue)}
.main-nav ul{list-style:none;position:absolute;left:118px;top:0;display:flex;height:27px;border-left:1px solid #2a66a0}
.main-nav li{height:27px;display:flex;align-items:center;padding:0 15px;font-size:9.4px;font-weight:700;color:#fff;border-right:1px solid #2a66a0}
.main-nav li.active{background:var(--teal)}

.hero{position:absolute;left:0;top:110px;width:882px;height:248px;background:var(--hero-bg)}
.hero-photo{position:absolute;left:0;top:0;width:400px;height:248px;background:linear-gradient(120deg,#c99a6a 0%,#a5683f 40%,#6d5a3b 75%,#4f5a2e 100%)}
.hero-title{position:absolute;left:470px;width:320px;top:46px;text-align:center;font-family:"Jost",sans-serif;font-weight:400;font-size:38px;line-height:46px;color:#111}
.hero-sub{position:absolute;left:470px;width:320px;top:138px;text-align:center;font-size:14px;line-height:17px;color:#222}
.hero-dots{position:absolute;left:610px;top:196px;display:flex;gap:4px}
.hero-dots span{width:8px;height:8px;border-radius:50%;background:#666}
.hero-dots span.on{background:var(--teal);width:9px;height:9px;margin-top:-.5px}

.breadcrumb{position:absolute;left:0;top:358px;width:882px;height:28px;background:var(--crumb);font-size:9.6px;color:#444;padding-left:118px;line-height:28px}
.breadcrumb strong{color:#222}

.faq-heading{position:absolute;left:0;top:412px;width:882px;text-align:center;font-family:"Jost",sans-serif;font-weight:400;font-size:25px;color:#222}
.faq-heading em{font-style:normal;color:var(--blue)}
.divider{position:absolute;left:269px;top:455px;width:344px;height:14px}
.divider:before,.divider:after{content:"";position:absolute;top:6px;width:157px;height:1px;background:#aaa}
.divider:before{left:0}.divider:after{right:0}
.divider i{position:absolute;left:166px;top:1px;width:12px;height:12px;border-radius:50%;border:1px solid #999}

.faq-list{position:absolute;left:118px;top:498px;width:646px}
.faq-item{border-bottom:1px solid var(--rule);padding-bottom:18px;margin-bottom:20px}
.faq-q,.faq-a{position:relative;padding-left:14px}
.faq-q{font-size:10.6px;font-weight:700;color:var(--blue);line-height:16px;margin-bottom:2px}
.faq-a{font-size:8.95px;line-height:14.2px;color:#333}
.faq-q:before,.faq-a:before{position:absolute;left:1px;font-size:8px;font-weight:700;color:var(--blue)}
.faq-q:before{content:"Q."}
.faq-a:before{content:"A.";top:0}
.faq-a p+p{margin-top:14px}

.site-footer{position:absolute;left:0;top:961px;width:882px;height:205px;background:var(--footer);color:var(--footer-text)}
.footer-col{position:absolute;top:30px}
.footer-title{font-family:"Jost",sans-serif;font-weight:400;font-size:13.5px;color:#fff;padding-bottom:10px;border-bottom:1px solid var(--footer-rule);margin-bottom:10px}
.footer-title em{font-style:normal;color:var(--teal)}
.quick-links{left:118px;width:89px}
.quick-links ul{list-style:none}
.quick-links li{font-size:9.2px;line-height:14.9px;padding-left:9px;position:relative}
.quick-links li:before{content:"›";position:absolute;left:0;color:#777}
.quick-links li.current{color:var(--teal)}
.contact-details{left:239px;width:158px;font-size:9.2px;line-height:13.5px}
.contact-details .org{color:#fff;margin-bottom:3px}
.contact-line{display:flex;align-items:center;gap:7px;font-size:11.5px;margin-top:8px}
.contact-line.mail{font-size:9.5px;margin-top:12px}
.follow-us{left:417px;width:166px}
.social li{list-style:none;display:flex;align-items:center;gap:10px;font-size:9.2px;height:27px;margin-left:5px;margin-top:3px}
.social li span{width:22px;height:22px;border-radius:50%;border:1.5px solid #fff}
.footer-brand{position:absolute;left:605px;top:92px;width:170px;text-align:center;font-family:"Open Sans",Arial,sans-serif;font-weight:400;font-size:17px;line-height:22px;color:var(--footer-brand);white-space:nowrap}

.copyright{position:absolute;left:0;top:1166px;width:882px;height:34px;background:var(--teal);color:#fff;font-size:9.2px;line-height:34px;padding-left:120px}
</style>
</head>
<body>

<header class="site-header">
  <a class="brand" href="#"><span class="brand-mark"></span><span class="brand-name">VitaPath Wellness</span></a>
  <div class="header-phone">
    <span class="phone-badge"><svg width="12" height="12" viewBox="0 0 24 24"><path fill="#fff" d="M6.6 10.8a15 15 0 0 0 6.6 6.6l2.2-2.2a1 1 0 0 1 1-.25 11.4 11.4 0 0 0 3.6.6 1 1 0 0 1 1 1V20a1 1 0 0 1-1 1A17 17 0 0 1 3 4a1 1 0 0 1 1-1h3.5a1 1 0 0 1 1 1c0 1.25.2 2.45.57 3.57a1 1 0 0 1-.25 1z"/></svg></span>
    555-214-0187
  </div>
  <a class="cta-button" href="#"><svg width="12" height="12" viewBox="0 0 12 12"><rect x="1" y="2" width="10" height="9" fill="none" stroke="#fff"/><path d="M1 5h10M4 1v2M8 1v2" stroke="#fff"/></svg>MAKE AN APPOINTMENT</a>
</header>

<nav class="main-nav">
  <ul>
    <li>HOME</li><li>ABOUT VITAPATH</li><li>OUR COURSES</li><li>SPECIAL OFFERS</li><li>TESTIMONIALS</li><li>BLOG</li><li class="active">FAQ'S</li><li>CONTACT US</li>
  </ul>
</nav>

<section class="hero">
  <div class="hero-photo" role="img" aria-label="Smiling couple cooking fresh vegetables together in a warm kitchen"></div>
  <h1 class="hero-title">VitaPath<br>Wellness</h1>
  <p class="hero-sub">Get the health and lifestyle<br>you want now!</p>
  <div class="hero-dots"><span class="on"></span><span></span><span></span><span></span></div>
</section>

<div class="breadcrumb">Home / <strong>FAQ's</strong></div>

<h2 class="faq-heading">Frequently Ask <em>Questions</em></h2>
<div class="divider"><i></i></div>

<main class="faq-list">
  <article class="faq-item">
    <h3 class="faq-q">What Is Type 2 Diabetes?</h3>
    <div class="faq-a"><p>Type 2 diabetes is the most common form of diabetes. Most of the food we eat is turned into glucose, or sugar, for our bodies to use for energy. The pancreas, an organ that lies near the stomach, makes a hormone called insulin to help glucose get into the cells of our bodies. When you have type 2 diabetes, your body can't use its own insulin as well as it should. This causes sugar to build up in your blood. Type 2 diabetes is a serious condition. It can lead to health issues such as heart attack; stroke; blindness; kidney failure; or loss of toes, feet, or legs.</p></div>
  </article>
  <article class="faq-item">
    <h3 class="faq-q">What Is Prediabetes?</h3>
    <div class="faq-a">
      <p>Prediabetes is a blood glucose (sugar) level that is higher than normal but not high enough to be diagnosed as diabetes. One in three American adults has prediabetes, and most do not even know they have it. If you have prediabetes and do not lose weight or do moderate physical activity, you can develop type 2 diabetes within 5 years.</p>
      <p>Am I at Risk for Prediabetes and Type 2 Diabetes?<br>You are at increased risk for developing prediabetes and type 2 diabetes if you:<br>• Are 45 years of age or older;<br>• Are overweight;<br>• Have a family history of type 2 diabetes;<br>• Are physically active fewer than three times per week; or<br>• Ever had diabetes while pregnant (gestational diabetes) or gave birth to a baby that weighed more than 9 pounds.<br>If you think you may be at risk, a health care provider can do a blood test to see if you have diabetes or pre diabetes.<br>Here is an online quiz to see if you are at risk www.stepaheadt2.example/quiz.</p>
    </div>
  </article>
  <article class="faq-item">
    <h3 class="faq-q">Does StepAhead T2 Work?</h3>
    <div class="faq-a"><p>The StepAhead T2 program can help people with prediabetes cut their risk of developing type 2 diabetes in half. The Diabetes Prevention Program research study showed that making modest behavior changes helped participants lose 5 to 7 percent of their body weight — that is 10 to 14 pounds for a person weighing 200 pounds. These lifestyle changes reduced the risk of developing type 2 diabetes by 58 percent in people with pre diabetes.</p></div>
  </article>
</main>

<footer class="site-footer">
  <div class="footer-col quick-links">
    <h4 class="footer-title">QUICK <em>LINKS</em></h4>
    <ul>
      <li class="current">Home</li><li>About VitaPath</li><li>Our Courses</li><li>Special Offers</li><li>Testimonials</li><li>Blog</li><li>Faq's</li><li>Contact Us</li>
    </ul>
  </div>
  <div class="footer-col contact-details">
    <h4 class="footer-title">CONTACT <em>DETAILS</em></h4>
    <p class="org">VITAPATH WELLNESS</p>
    <p>123, Lorem Ipsum Dollar Smit Amet,<br>Nibh Nonumy. Golham - 123 456</p>
    <p class="contact-line"><svg width="11" height="11" viewBox="0 0 24 24"><path fill="#00a990" d="M6.6 10.8a15 15 0 0 0 6.6 6.6l2.2-2.2a1 1 0 0 1 1-.25 11.4 11.4 0 0 0 3.6.6 1 1 0 0 1 1 1V20a1 1 0 0 1-1 1A17 17 0 0 1 3 4a1 1 0 0 1 1-1h3.5a1 1 0 0 1 1 1c0 1.25.2 2.45.57 3.57a1 1 0 0 1-.25 1z"/></svg>555-214-0187</p>
    <p class="contact-line"><svg width="12" height="11" viewBox="0 0 12 11"><rect x="3" y="0" width="6" height="3" fill="#00a990"/><rect x="0" y="3" width="12" height="5" fill="#00a990"/><rect x="3" y="7" width="6" height="4" fill="#00a990"/></svg>555-214-0190</p>
    <p class="contact-line mail"><svg width="11" height="8" viewBox="0 0 11 8"><rect width="11" height="8" fill="#00a990"/><path d="M0 0l5.5 4.5L11 0" stroke="#1f2733" fill="none"/></svg>hello@vitapathwellness.example</p>
  </div>
  <div class="footer-col follow-us">
    <h4 class="footer-title">FOLLOW <em>US</em></h4>
    <ul class="social">
      <li><span></span>Friendbook</li>
      <li><span></span>Chirper</li>
      <li><span></span>Linkora</li>
      <li><span></span>Circlespace</li>
    </ul>
  </div>
  <div class="footer-brand">VitaPath Wellness</div>
</footer>

<div class="copyright">© 2016 VitaPath Wellness. All Rights Reserved.</div>

</body>
</html>
```